Harborline Auto LLC

Car Dealer Customer Service
Address: 2874 Cresthaven Road, Shelbyville, TN 37162
web: www.harborlineautoxq.net
email: harborlineautoxq@mailnest.example
Phone: (931) 555-0148
Phone: (629) 555-0173

```html
<!DOCTYPE html>
<html lang="en">
<head>
<meta charset="utf-8">
<title>Harborline Auto – Business Card</title>
<link href="https://fonts.googleapis.com/css2?family=Montserrat:wght@700;800&family=Arimo:wght@400&family=Bebas+Neue&display=swap" rel="stylesheet">
<style>
  :root {
    --page-bg: #e9e6e3;
    --card-blue-top: #2590c9;
    --card-blue-bottom: #1a76aa;
    --card-gold: #ebb141;
    --text-light: #ffffff;
    --divider: rgba(255,255,255,0.55);
    --seal-fill: #eef0f3;
    --brand-blue: #1f78b0;
  }
  * { margin: 0; padding: 0; box-sizing: border-box; }
  html, body { width: 1200px; height: 900px; overflow: hidden; background: var(--page-bg); }
  .card {
    position: absolute; left: 100px; top: 141px;
    width: 1000px; height: 618px; overflow: hidden;
    background: linear-gradient(180deg, var(--card-blue-top), var(--card-blue-bottom));
    box-shadow: 0 12px 30px rgba(0,0,0,0.18);
  }
  .card__gold-band {
    position: absolute; left: 698px; top: 0; right: 0; bottom: 0;
    background: var(--card-gold);
  }
  .brand-seal {
    position: absolute; left: 432px; top: 41px;
    width: 532px; height: 532px; border-radius: 50%;
    background: var(--seal-fill);
    display: flex; align-items: center; justify-content: center;
  }
  .brand-seal__name {
    font-family: "Montserrat", sans-serif; font-weight: 800;
    font-size: 37px; color: var(--brand-blue); letter-spacing: 0.5px;
  }
  .contact { position: absolute; left: 44px; top: 0; color: var(--text-light); font-family: "Arimo", sans-serif; }
  .contact__name {
    position: absolute; top: 72px; white-space: nowrap;
    font-family: "Montserrat", sans-serif; font-weight: 700; font-size: 37px; letter-spacing: 0.3px;
  }
  .contact__role { position: absolute; top: 114px; font-size: 28px; white-space: nowrap; }
  .contact__address { position: absolute; top: 226px; font-size: 27px; line-height: 37px; white-space: nowrap; }
  .contact__list { position: absolute; top: 339px; list-style: none; font-size: 22px; }
  .contact__item { display: flex; align-items: center; gap: 10px; height: 36px; white-space: nowrap; }
  .contact__icon { width: 26px; height: 26px; fill: none; stroke: var(--text-light); stroke-width: 2; }
  .card__divider {
    position: absolute; left: 44px; top: 502px; width: 429px; height: 1px;
    background: var(--divider);
  }
  .card__tagline {
    position: absolute; left: 42px; top: 518px;
    font-family: "Bebas Neue", sans-serif; font-size: 48px; color: var(--text-light);
    letter-spacing: 0.2px; white-space: nowrap;
  }
</style>
</head>
<body>
  <section class="card">
    <div class="card__gold-band"></div>

    <div class="brand-seal">
      <span class="brand-seal__name">HARBORLINE AUTO</span>
    </div>

    <div class="contact">
      <h1 class="contact__name">MARCUS DELANEY</h1>
      <p class="contact__role">Managing Director</p>
      <p class="contact__address">2874 Cresthaven Road<br>Shelbyville, TN 37162</p>
      <ul class="contact__list">
        <li class="contact__item">
          <svg class="contact__icon" viewBox="0 0 24 24"><path d="M5 3h4l2 5-2.5 1.5a11 11 0 0 0 6 6L16 13l5 2v4a2 2 0 0 1-2 2A16 16 0 0 1 3 5a2 2 0 0 1 2-2z"/></svg>
          (931) 555-0148
        </li>
        <li class="contact__item">
          <svg class="contact__icon" viewBox="0 0 24 24"><path d="M5 3h4l2 5-2.5 1.5a11 11 0 0 0 6 6L16 13l5 2v4a2 2 0 0 1-2 2A16 16 0 0 1 3 5a2 2 0 0 1 2-2z"/></svg>
          (629) 555-0173
        </li>
        <li class="contact__item">
          <svg class="contact__icon" viewBox="0 0 24 24"><circle cx="12" cy="12" r="9"/><path d="M3 12h18M12 3c3 3 3 15 0 18M12 3c-3 3-3 15 0 18"/></svg>
          www.harborlineautoxq.net
        </li>
        <li class="contact__item">
          <svg class="contact__icon" viewBox="0 0 24 24"><rect x="3" y="6" width="18" height="13"/><path d="M3 6l9 7 9-7"/></svg>
          harborlineautoxq@mailnest.example
        </li>
      </ul>
    </div>

    <div class="card__divider"></div>
    <p class="card__tagline">CAR DEALER CUSTOMER SERVICE</p>
  </section>
</body>
</html>
```